Im open to ideas.. I was thinking on my business cards aswell as my logo. a place for my name. email. phone number and abn..

ive attched a file with my business logo. which i dont love the colours.. i was think a dark background with charcoal letters so something along those colour schumes but im open to ideas..

BRM Constructions

```html
<!DOCTYPE html>
<html lang="en">
<head>
<meta charset="UTF-8">
<title>BRM Constructions – Business Card</title>
<link href="https://fonts.googleapis.com/css2?family=Roboto+Slab:wght@400;500&display=swap" rel="stylesheet">
<style>
  :root {
    --page-bg: #c9c9c9;
    --stone-dark: #232323;
    --stone-mid: #3a3a3a;
    --stone-light: #4a4a48;
    --text-light: #f2f2f2;
    --text-muted: #d6d6d6;
    --rule: #cfcfcf;
    --wordmark: #c4c6c8;
  }
  * { box-sizing: border-box; margin: 0; padding: 0; }
  html, body {
    width: 1200px;
    height: 800px;
    overflow: hidden;
    background: var(--page-bg);
  }
  .business-card {
    position: absolute;
    left: 75px;
    top: 100px;
    width: 1050px;
    height: 600px;
    border-radius: 48px;
    overflow: hidden;
    font-family: "Roboto Slab", serif;
    color: var(--text-light);
  }
  .card-texture {
    position: absolute;
    inset: 0;
    background:
      radial-gradient(ellipse at 30% 35%, var(--stone-light) 0%, transparent 55%),
      radial-gradient(ellipse at 75% 70%, var(--stone-mid) 0%, transparent 60%),
      linear-gradient(160deg, var(--stone-mid), var(--stone-dark));
  }
  .card-content {
    position: relative;
    height: 100%;
  }
  .wordmark {
    position: absolute;
    top: 150px;
    left: 0;
    right: 0;
    text-align: center;
    font-size: 64px;
    font-weight: 500;
    letter-spacing: 4px;
    color: var(--wordmark);
  }
  .rule {
    position: absolute;
    height: 1.5px;
    background: var(--rule);
  }
  .rule--upper { top: 318px; left: 330px; width: 520px; }
  .rule--lower { top: 458px; left: 200px; width: 520px; }
  .person-name {
    position: absolute;
    top: 332px;
    left: 0; right: 0;
    text-align: center;
    font-size: 40px;
    font-weight: 400;
  }
  .abn {
    position: absolute;
    top: 392px;
    left: 0; right: 0;
    text-align: center;
    font-size: 22px;
    color: var(--text-muted);
  }
  .contact-list {
    position: absolute;
    top: 478px;
    left: 0; right: 0;
    list-style: none;
    display: flex;
    flex-direction: column;
    align-items: center;
    gap: 12px;
    font-size: 30px;
  }
  .contact-item {
    display: flex;
    align-items: center;
    gap: 10px;
  }
  .contact-icon { width: 30px; height: 30px; flex: none; }
</style>
</head>
<body>
  <article class="business-card">
    <div class="card-texture" role="img" aria-label="Dark charcoal slate stone texture"></div>
    <div class="card-content">
      <div class="wordmark">BRM Constructions</div>
      <div class="rule rule--upper"></div>
      <h1 class="person-name">Dane Morrow</h1>
      <p class="abn">ABN: 51 382 619 047</p>
      <div class="rule rule--lower"></div>
      <ul class="contact-list">
        <li class="contact-item">
          <svg class="contact-icon" viewBox="0 0 30 30" aria-hidden="true">
            <circle cx="15" cy="15" r="14" fill="#f2f2f2"/>
            <rect x="8" y="10" width="14" height="10" rx="1" fill="none" stroke="#2a2a2a" stroke-width="1.6"/>
            <path d="M8 10.5 L15 16 L22 10.5" fill="none" stroke="#2a2a2a" stroke-width="1.6"/>
          </svg>
          <span>dane.morrow@brmbuild.com</span>
        </li>
        <li class="contact-item">
          <svg class="contact-icon" viewBox="0 0 30 30" aria-hidden="true">
            <circle cx="15" cy="15" r="14" fill="#f2f2f2"/>
            <path d="M10.5 8.5c1-.6 1.8-.4 2.3.5l1.2 2.2c.4.8.2 1.5-.5 2l-.9.6c.7 1.7 2 3 3.6 3.7l.6-.9c.5-.7 1.2-.9 2-.5l2.2 1.2c.9.5 1.1 1.3.5 2.3-.8 1.4-2.2 2-3.8 1.5-3.7-1.2-6.3-3.8-7.5-7.5-.5-1.6.1-3 1.3-3.6z" fill="#2a2a2a"/>
          </svg>
          <span>202-555-0173</span>
        </li>
      </ul>
    </div>
  </article>
</body>
</html>
```